Buch-/eBook-Cover für einen Elternratgeber
Zielgruppe
Buch: Elternratgeber
Titel: Werte lernen
Untertitel: Deinem Kind den richtigen Umgang beibringen
Wir sind der BRAM Verlag und suchen ein passendes Cover für unseren neuen Elternratgeber. Mit diesem Buch möchten wir Eltern unterstützen, ihren Kindern einen guten und verantwortungsvollen Umgang mit Geld zu vermitteln.
Anforderungen an das Cover-Design:
Bitte keinen Comicstil
Das Buch richtet sich an Eltern (nicht kindlich oder verspielt gestalten)
Keine direkte Darstellung von Geld (z. B. keine Münzen, Geldscheine, Sparschweine usw.)
Ob mit oder ohne Personen auf dem Cover: sind wir offen
Farbwahl und Bildsprache: gerne seriös, ansprechend und modern
Wir sind gespannt auf kreative und professionelle Vorschläge!
E-Book E-Book"
Das Design darf nicht zu überladen sein.

```html
<!DOCTYPE html>
<html lang="de">
<head>
<meta charset="utf-8">
<title>Werte lernen – Cover</title>
<link rel="stylesheet" href="https://fonts.googleapis.com/css2?family=Frank+Ruhl+Libre:wght@500&family=Inter:wght@400;600&display=swap">
<style>
  :root {
    --paper: #ecebe6;
    --ink: #1c1b1a;
    --green-dark: #15251e;
    --green-light: #84a895;
    --black-top: #0d0d0d;
    --black-bottom: #6e6669;
    --brown-top: #5b4a42;
    --brown-bottom: #cba77b;
    --stone-light: #e2e2e0;
    --stone-dark: #b4b4b2;
    --skin-light: #c99277;
    --skin-dark: #a7735a;
    --portrait-bg: #f4f2ef;
  }
  * { margin: 0; padding: 0; box-sizing: border-box; }
  html, body { width: 1200px; height: 900px; overflow: hidden; background: var(--paper); }
  .cover {
    position: relative;
    width: 1200px;
    height: 900px;
    background: var(--paper);
    color: var(--ink);
    font-family: "Inter", Arial, sans-serif;
  }
  .author {
    position: absolute;
    left: 100px;
    top: 68px;
    font-size: 21px;
    font-weight: 400;
  }
  .title {
    position: absolute;
    left: 96px;
    top: 200px;
    font-family: "Frank Ruhl Libre", Georgia, serif;
    font-weight: 500;
    font-size: 120px;
    line-height: 104px;
    letter-spacing: -1.5px;
  }
  .subtitle {
    position: absolute;
    left: 100px;
    top: 438px;
    font-size: 27px;
    line-height: 36px;
    font-weight: 400;
  }
  .imprint {
    position: absolute;
    left: 100px;
    top: 814px;
    font-size: 24px;
    font-weight: 600;
  }
  .publisher {
    position: absolute;
    right: 52px;
    top: 812px;
    display: flex;
    align-items: center;
    gap: 8px;
    font-size: 17px;
    font-weight: 600;
  }
  .publisher-dot {
    width: 22px;
    height: 22px;
    border: 3px solid var(--ink);
    border-radius: 50%;
  }
  .artwork { position: absolute; left: 0; top: 0; }
</style>
</head>
<body>
<div class="cover">
  <p class="author">Marlene Oster</p>

  <h1 class="title">Werte<br>lernen</h1>
  <p class="subtitle">Deinem Kind den<br>richtigen<br>Umgang beibringen.</p>

  <svg class="artwork" width="1200" height="900" viewBox="0 0 1200 900">
    <defs>
      <linearGradient id="green-fade" x1="0" y1="0" x2="0" y2="1">
        <stop offset="0" stop-color="var(--green-dark)"/>
        <stop offset="1" stop-color="var(--green-light)"/>
      </linearGradient>
      <linearGradient id="black-fade" x1="0" y1="0" x2="0" y2="1">
        <stop offset="0" stop-color="var(--black-top)"/>
        <stop offset="1" stop-color="var(--black-bottom)"/>
      </linearGradient>
      <linearGradient id="brown-fade" x1="0" y1="0" x2="0" y2="1">
        <stop offset="0" stop-color="var(--brown-top)"/>
        <stop offset="1" stop-color="var(--brown-bottom)"/>
      </linearGradient>
      <linearGradient id="stone-fade" x1="0" y1="0" x2="0" y2="1">
        <stop offset="0" stop-color="var(--stone-light)"/>
        <stop offset="1" stop-color="var(--stone-dark)"/>
      </linearGradient>
      <linearGradient id="skin-fade" x1="0" y1="0" x2="0" y2="1">
        <stop offset="0" stop-color="var(--skin-light)"/>
        <stop offset="1" stop-color="var(--skin-dark)"/>
      </linearGradient>
    </defs>

    <circle class="portrait" cx="860" cy="146" r="118" fill="var(--portrait-bg)"
            role="img" aria-label="Foto eines kleinen Kindes, das über den Rand nach unten schaut"/>

    <rect class="hands-photo" x="594" y="568" width="536" height="286" rx="60" fill="url(#skin-fade)"
          role="img" aria-label="Foto zweier Hände, die die Treppe von unten tragen"/>

    <path class="shape-green" d="M979,208 V477 H797 A132,132 0 0 1 665,345 V340 A132,132 0 0 1 797,208 Z" fill="url(#green-fade)"/>
    <path class="shape-black" d="M979,342 H997 A145,145 0 0 1 997,631 H979 Z" fill="url(#black-fade)"/>
    <path class="shape-brown" d="M833,461 H730 A103,103 0 0 0 627,564 V564 A103,103 0 0 0 730,667 H833 Z" fill="url(#brown-fade)"/>

    <rect class="staircase-photo" x="740" y="342" width="239" height="441" fill="url(#stone-fade)"
          role="img" aria-label="Foto einer Marmortreppe, die nach oben führt"/>
  </svg>

  <p class="imprint">Faronis</p>
  <div class="publisher"><span class="publisher-dot"></span>BRAM</div>
</div>
</body>
</html>
```